Business cards in digital learning for freelancer

Hello, I need a business cards in french. I work in the Digital learning industries as freeelancer; I'm an expert in digital learning. I work in France. My customer are in the health industry, pharmaceutical industry, and training organization. I've got a logo. I offer three services: consulting, Design, and Training. In the consulting, I offers coaching to choose your digital learning tools and the digital learning strategy. For the Design, I product differents level of elearning like rapid-learning, elearning, micro-learning, video-learning. And for the training service, I've create training about pedagogy, digital learning management project, Digital learning design.
I join my Logo create in this platform. My universe is gamified. I like the life, and I'm very social. I want a card like I'm I. I love Art (painting), Europeen comics. I use in my visual support "permanent maker" font and caracters. I would like cards: elegant, modern, Top class. If you need any information, you can ask me.
thanks for ideas

Target Market(s)

in health industries and training organization for Training manager, instructor, human resources director

Contact Information for Business Card

Phone number : 06 71 38 95 14 , mail: bastiengolmier@quelmoto.fr, web: bastiengolmier.fr , Carrivo

Font styles to use
Sans Serif

Requirements
Must have
• Use my logo and write my 3 services (consulting, training, design)

```html
<!DOCTYPE html>
<html lang="fr">
<head>
<meta charset="utf-8">
<title>Golmier – cartes de visite</title>
<link href="https://fonts.googleapis.com/css2?family=Montserrat:wght@400;600;700&family=Cinzel:wght@400&display=swap" rel="stylesheet">
<style>
  :root {
    --orange: #f37324;
    --grey: #7a7a7a;
    --white: #ffffff;
    --ink: #1c1c1c;
    --backdrop: #262626;
  }
  html, body {
    margin: 0;
    width: 1200px;
    height: 1015px;
    overflow: hidden;
    background: var(--backdrop);
  }
  .sheet {
    position: relative;
    width: 1200px;
    height: 1015px;
  }
  .card {
    position: absolute;
    left: 250px;
    width: 700px;
    height: 400px;
    background: var(--white);
    overflow: hidden;
    font-family: 'Montserrat', sans-serif;
  }
  .card--front { top: 92px; }
  .card--back  { top: 522px; }
  .card__waves {
    position: absolute;
    inset: 0;
    width: 700px;
    height: 400px;
  }
  .services {
    position: absolute;
    left: 48px;
    top: 58px;
    margin: 0;
    padding: 0;
    list-style: none;
    color: var(--white);
    font-size: 19px;
    letter-spacing: 0.5px;
    line-height: 30px;
  }
  .services li::before {
    content: "";
    display: inline-block;
    width: 9px;
    height: 9px;
    margin-right: 8px;
    border-radius: 50%;
    background: var(--white);
    vertical-align: middle;
  }
  .brand {
    position: absolute;
    display: flex;
    align-items: center;
    gap: 12px;
    height: 56px;
  }
  .card--front .brand { right: 44px; top: 205px; }
  .card--back  .brand { left: 44px;  top: 140px; }
  .brand__dot {
    width: 30px;
    height: 30px;
    border-radius: 50%;
    background: var(--orange);
  }
  .brand__name {
    color: var(--orange);
    font-weight: 700;
    font-size: 44px;
    letter-spacing: 2px;
    text-transform: uppercase;
    line-height: 1;
  }
  .holder {
    position: absolute;
    right: 46px;
    top: 44px;
    text-align: right;
  }
  .holder__name {
    margin: 0;
    font-family: 'Cinzel', serif;
    font-weight: 400;
    color: var(--orange);
    font-size: 30px;
    letter-spacing: 1px;
  }
  .holder__role {
    margin: 2px 0 0;
    color: var(--ink);
    font-size: 18px;
  }
  .contact {
    position: absolute;
    right: 36px;
    bottom: 40px;
    margin: 0;
    padding: 0;
    list-style: none;
    color: var(--white);
    font-size: 17px;
    line-height: 27px;
    text-align: right;
  }
  .contact li {
    display: flex;
    justify-content: flex-end;
    align-items: center;
    gap: 10px;
  }
  .contact svg { width: 18px; height: 18px; flex: none; }
  .social {
    position: absolute;
    right: 36px;
    bottom: 138px;
    display: flex;
    align-items: center;
    gap: 8px;
    color: var(--white);
    font-size: 15px;
    font-weight: 600;
  }
  .social__dot {
    width: 22px;
    height: 22px;
    border-radius: 50%;
    background: var(--white);
  }
</style>
</head>
<body>
<main class="sheet">

  <section class="card card--front">
    <svg class="card__waves" viewBox="0 0 700 400" aria-hidden="true">
      <path d="M0 0 H700 V26 C590 18 500 40 420 110 C340 180 280 262 60 282 H0 Z" fill="var(--orange)"/>
      <path d="M700 16 C590 8 500 30 410 100 C330 170 270 252 50 272" fill="none" stroke="var(--white)" stroke-width="4"/>
      <path d="M700 42 C600 34 514 56 436 124 C370 184 330 240 240 272" fill="none" stroke="var(--grey)" stroke-width="5"/>
    </svg>
    <ul class="services">
      <li>CONSULTING</li>
      <li>TRAINING</li>
      <li>DESIGN</li>
    </ul>
    <div class="brand">
      <span class="brand__dot"></span>
      <span class="brand__name">Golmier</span>
    </div>
  </section>

  <section class="card card--back">
    <svg class="card__waves" viewBox="0 0 700 400" aria-hidden="true">
      <g transform="rotate(180 350 200)">
        <path d="M0 0 H700 V26 C590 18 500 40 420 110 C340 180 280 262 60 282 H0 Z" fill="var(--orange)"/>
        <path d="M700 16 C590 8 500 30 410 100 C330 170 270 252 50 272" fill="none" stroke="var(--white)" stroke-width="4"/>
        <path d="M700 42 C600 34 514 56 436 124 C370 184 330 240 240 272" fill="none" stroke="var(--grey)" stroke-width="5"/>
      </g>
    </svg>
    <div class="holder">
      <h1 class="holder__name">LUCIEN MARCHAL</h1>
      <p class="holder__role">Managing Director</p>
    </div>
    <div class="brand">
      <span class="brand__dot"></span>
      <span class="brand__name">Golmier</span>
    </div>
    <div class="social">
      <span>Carrivo</span>
      <span class="social__dot"></span>
    </div>
    <ul class="contact">
      <li>06 71 38 95 14
        <svg viewBox="0 0 24 24" aria-hidden="true"><path d="M6 3 L9 3 L10.5 7.5 L8.5 9 C9.5 11.5 12.5 14.5 15 15.5 L16.5 13.5 L21 15 L21 18 C21 19.5 19.5 21 18 21 C10 20.5 3.5 14 3 6 C3 4.5 4.5 3 6 3 Z" fill="var(--white)"/></svg>
      </li>
      <li>bastiengolmier@quelmoto.fr
        <svg viewBox="0 0 24 24" aria-hidden="true"><rect x="2" y="5" width="20" height="14" fill="var(--white)"/><path d="M2 5 L12 13 L22 5" fill="none" stroke="var(--orange)" stroke-width="1.8"/></svg>
      </li>
      <li>www.bastiengolmier.fr
        <svg viewBox="0 0 24 24" aria-hidden="true"><circle cx="12" cy="12" r="9.5" fill="none" stroke="var(--white)" stroke-width="2"/><ellipse cx="12" cy="12" rx="4" ry="9.5" fill="none" stroke="var(--white)" stroke-width="1.6"/><path d="M2.5 12 H21.5 M4 7.5 H20 M4 16.5 H20" stroke="var(--white)" stroke-width="1.6"/></svg>
      </li>
    </ul>
  </section>

</main>
</body>
</html>
```